REDESIGN MAIN BANNER IMAGE FOR MARKETING WEBSITE

I feel like my main banner image is too busy but I like it but i want to see other options. www.brightlanepromoworks.biz I want a nice professional clean design that goes with current theme of site. Must look professional and show the variety of incentives we offer but not be overwelming.

My business is called Brightlane Promo Works and I provide businesses around the world with marketing incentives that they can use to create exciting promotions and contest and marketing giveaways to help attract more customers.

I provide a variety of different types of incentives such as Vacation Certificates, Dining Vouchers, Hotel Savings Cards, Smart Watches, Etc. that businesses can use in their marketing efforts.

I want my main banner image to reflect the variety of different categories of incentives... that I offer here: https://www.brightlanepromoworks.biz/incentives

We can use images of certificates or images.....I just want the content to be the same:

CONTENT FOR MAIN BANNER IMAGE:
INCREASE LEADS AND SALES OVERNIGHT

CREATE EXCITING MARKETING PROMOTIONS GIVING AWAY SMART DEVICES, VACATION CERTIFICATES, DINING VOUCHERS AND OTHER INCENTIVES TO YOUR CUSTOMERS

GET A FREE SAMPLE PACKAGE FOR A LIMITED TIME ONLY

Target Market(s)

b2b business owners, ceo, president, owner, founder

Industry/Entity Type

Promotional

Requirements
Must have
• Hi guys keep in mind the finished product will have to be 1800x840

Nice to have
• I want a nice professional clean design that goes with current theme of site. Must look professional and show the variety of incentives we offer but not be overwelming.
Should not have

```html
<!DOCTYPE html>
<html lang="en">
<head>
<meta charset="utf-8">
<title>Brightlane Promo Works – Main Banner</title>
<link rel="stylesheet" href="https://fonts.googleapis.com/css2?family=Bebas+Neue&family=Montserrat:wght@300;400;700&display=swap">
<style>
  :root {
    --page-bg: #e4e4e4;
    --banner-bg: #f1f1f1;
    --stripe-light: #f8f8f8;
    --brand-blue: #0d56a6;
    --text-blue: #0b4c9c;
    --headline-red: #f21d24;
    --offer-green: #4caf50;
    --offer-green-text: #3aa53a;
    --free-lavender: #c9c6f2;
    --panel-grey: #a9a9a9;
    --card-red: #c3161c;
    --tag-yellow: #ffd21a;
    --line-grey: #c9c9c9;
    --white: #ffffff;
  }
  * { margin: 0; padding: 0; box-sizing: border-box; }
  html, body { width: 1200px; height: 764px; overflow: hidden; background: var(--page-bg); }
  .banner {
    position: absolute; left: 0; top: 128px;
    width: 1200px; height: 508px;
    background: var(--banner-bg);
    overflow: hidden;
  }
  .banner__shapes { position: absolute; inset: 0; }

  .headline {
    position: absolute; left: 53px; top: 72px;
    font-family: "Bebas Neue", "Oswald", sans-serif;
    font-weight: 400;
    font-size: 76px; line-height: 64px;
    color: var(--headline-red);
    letter-spacing: 3.2px;
  }
  .subline {
    position: absolute; left: 53px; top: 204px; width: 620px;
    font-family: "Montserrat", sans-serif;
    font-size: 14.6px; line-height: 23.4px;
    color: var(--text-blue);
    text-transform: uppercase;
  }
  .offer {
    position: absolute; left: 91px; top: 298px;
    font-family: "Bebas Neue", "Oswald", sans-serif;
    font-size: 28px; color: var(--text-blue);
    white-space: nowrap; letter-spacing: 0.3px;
  }
  .offer__free { font-size: 42px; color: var(--offer-green-text); }
  .offer__limited { color: var(--headline-red); }

  .cta {
    position: absolute; left: 155px; top: 355px; width: 402px; height: 112px;
  }
  .cta__shape { position: absolute; inset: 0; }
  .cta__label {
    position: absolute; left: 0; right: 0; top: 12px; text-align: center;
    font-family: "Montserrat", sans-serif; font-weight: 700;
    font-size: 36px; color: var(--white); letter-spacing: 0.5px;
  }
  .cta__sub {
    position: absolute; left: -20px; right: 0; top: 52px; text-align: center;
    font-family: "Montserrat", sans-serif; font-weight: 300;
    font-size: 25px; color: var(--free-lavender);
  }

  .incentive-panel {
    position: absolute; left: 643px; top: 45px; width: 537px; height: 417px;
    background: var(--panel-grey);
    display: grid;
    grid-template-columns: repeat(5, 98px);
    grid-template-rows: repeat(3, 130px);
    gap: 6px 6px;
    padding: 8px 12px;
  }
  .incentive-card {
    position: relative;
    background: var(--white);
    overflow: hidden;
    display: flex; flex-direction: column;
  }
  .incentive-card__photo {
    position: relative; height: 46px;
    padding: 3px 4px;
  }
  .incentive-card__title {
    font-family: "Bebas Neue", "Oswald", sans-serif;
    font-size: 13px; line-height: 12px; color: var(--white);
    display: flex; align-items: center; gap: 3px;
  }
  .incentive-card__tag {
    font-size: 7px; line-height: 8px; padding: 0 2px;
    background: var(--card-red); color: var(--tag-yellow);
    letter-spacing: 0.2px; white-space: nowrap;
  }
  .incentive-card__note {
    margin-top: 2px;
    font-family: "Montserrat", sans-serif; font-weight: 700;
    font-size: 4.6px; line-height: 5.4px; color: var(--white);
    width: 62px;
  }
  .incentive-card__band {
    height: 7px; background: var(--card-red);
    border-radius: 0 0 60% 0 / 0 0 100% 0;
  }
  .incentive-card__body {
    position: relative; flex: 1;
    margin: 4px 24px 0 4px;
    background: repeating-linear-gradient(180deg, var(--line-grey) 0 1.5px, transparent 1.5px 4px);
  }
  .incentive-card__body::before {
    content: ""; position: absolute; left: 0; top: 18px; width: 26px; height: 3px;
    background: var(--card-red);
  }
  .incentive-card__body::after {
    content: ""; position: absolute; left: 0; top: 40px; width: 26px; height: 3px;
    background: var(--card-red);
  }
  .incentive-card__thumbs {
    position: absolute; right: 3px; top: 44px;
    display: flex; flex-direction: column; gap: 3px;
  }
  .incentive-card__thumbs span {
    width: 17px; height: 17px; border-radius: 50%;
    border: 2px solid var(--card-red);
    background: var(--thumb, #8a9bb0);
  }
  .incentive-card__footer {
    height: 16px; margin: 3px 4px 3px;
    border-top: 1px solid var(--line-grey);
    background:
      linear-gradient(var(--card-red), var(--card-red)) 2px 5px / 18px 2px no-repeat,
      linear-gradient(var(--line-grey), var(--line-grey)) 30px 4px / 56px 1.5px no-repeat,
      linear-gradient(var(--card-red), var(--card-red)) 30px 8px / 56px 2px no-repeat,
      linear-gradient(var(--line-grey), var(--line-grey)) 40px 12px / 36px 1.5px no-repeat;
  }

  .theme-casino  .incentive-card__photo { background: linear-gradient(160deg, #2a1e5c, #8a2c6e 60%, #d9862e); } .theme-casino  { --thumb: #c9683a; }
  .theme-hotel   .incentive-card__photo { background: linear-gradient(160deg, #3a2c24, #7a6252 55%, #b49a80); } .theme-hotel   { --thumb: #5f86a8; }
  .theme-cruise  .incentive-card__photo { background: linear-gradient(180deg, #6ea2d6, #2f5f97 60%, #1c3b66); } .theme-cruise  { --thumb: #3d8fc4; }
  .theme-dining  .incentive-card__photo { background: linear-gradient(160deg, #2b1a12, #8a4a22 55%, #d7a15c); } .theme-dining  { --thumb: #a4552c; }
  .theme-tablet  .incentive-card__photo { background: linear-gradient(150deg, #0c0c0c, #2c2c2c 55%, #6fbf3a); } .theme-tablet  { --thumb: #9aa3ab; }
  .theme-player  .incentive-card__photo { background: linear-gradient(160deg, #3b4658, #6f7c90 55%, #b9a89a); } .theme-player  { --thumb: #4a8fd0; }
  .theme-speaker .incentive-card__photo { background: linear-gradient(180deg, #9cc4e4, #d8c39a 60%, #1c5fa8); } .theme-speaker { --thumb: #2f6fb8; }
  .theme-card    .incentive-card__photo { background: linear-gradient(160deg, #d9e6f0, #9fc0d8 55%, #e3b98e); } .theme-card    { --thumb: #e08a3a; }
  .theme-air     .incentive-card__photo { background: linear-gradient(180deg, #7fb4e6, #c9def2 60%, #8aa2bc); } .theme-air     { --thumb: #5c7fa3; }
  .theme-shop    .incentive-card__photo { background: linear-gradient(160deg, #1b2838, #3c5068 55%, #7d8ea3); } .theme-shop    { --thumb: #d4473a; }
</style>
</head>
<body>
  <section class="banner">
    <svg class="banner__shapes" width="1200" height="508" viewBox="0 0 1200 508">
      <polygon points="240,0 330,0 60,508 -30,508" fill="var(--stripe-light)"/>
      <polygon points="420,0 470,0 200,508 150,508" fill="var(--stripe-light)"/>
      <polygon points="0,0 101,0 0,131" fill="var(--brand-blue)"/>
      <polygon points="1016,0 1174,0 835,508 677,508" fill="var(--brand-blue)"/>
    </svg>

    <h1 class="headline">Increase leads and<br>sales overnight</h1>

    <p class="subline">Create exciting marketing promotions giving away smart devices,<br>vacation certificates, dining vouchers and other incentives to<br>your customers</p>

    <p class="offer">Get a <span class="offer__free">Free</span> sample package for a <span class="offer__limited">limited time</span> only</p>

    <div class="cta">
      <svg class="cta__shape" width="402" height="112" viewBox="0 0 402 112">
        <ellipse cx="200" cy="100" rx="190" ry="8" fill="#000" opacity="0.08"/>
        <path d="M4,2 L398,0 L392,82 Q260,86 190,96 Q110,86 10,82 Z" fill="var(--offer-green)"/>
      </svg>
      <span class="cta__label">GET FREE SAMPLE</span>
      <span class="cta__sub">100% FREE</span>
    </div>

    <div class="incentive-panel">
      <article class="incentive-card theme-casino">
        <div class="incentive-card__photo" role="img" aria-label="Resort and casino skyline at night">
          <p class="incentive-card__title">Enjoy <span class="incentive-card__tag">4 NIGHTS</span></p>
          <p class="incentive-card__note">Resort / Casino Accommodations</p>
        </div>
        <div class="incentive-card__band"></div>
        <div class="incentive-card__body"></div>
        <div class="incentive-card__thumbs" role="img" aria-label="Small resort photos"><span></span><span></span><span></span></div>
        <div class="incentive-card__footer"></div>
      </article>
      <article class="incentive-card theme-hotel">
        <div class="incentive-card__photo" role="img" aria-label="Hotel suite interior">
          <p class="incentive-card__title">Enjoy <span class="incentive-card__tag">HOTEL STAY</span></p>
          <p class="incentive-card__note">3-Star Hotel Accommodations</p>
        </div>
        <div class="incentive-card__band"></div>
        <div class="incentive-card__body"></div>
        <div class="incentive-card__thumbs" role="img" aria-label="Small hotel photos"><span></span><span></span><span></span></div>
        <div class="incentive-card__footer"></div>
      </article>
      <article class="incentive-card theme-hotel">
        <div class="incentive-card__photo" role="img" aria-label="Hotel suite interior">
          <p class="incentive-card__title">Enjoy <span class="incentive-card__tag">HOTEL STAY</span></p>
          <p class="incentive-card__note">3-Star Hotel Accommodations</p>
        </div>
        <div class="incentive-card__band"></div>
        <div class="incentive-card__body"></div>
        <div class="incentive-card__thumbs" role="img" aria-label="Small hotel photos"><span></span><span></span><span></span></div>
        <div class="incentive-card__footer"></div>
      </article>
      <article class="incentive-card theme-hotel">
        <div class="incentive-card__photo" role="img" aria-label="Hotel suite interior">
          <p class="incentive-card__title">Enjoy <span class="incentive-card__tag">HOTEL STAY</span></p>
          <p class="incentive-card__note">3-Star Hotel Accommodations</p>
        </div>
        <div class="incentive-card__band"></div>
        <div class="incentive-card__body"></div>
        <div class="incentive-card__thumbs" role="img" aria-label="Small hotel photos"><span></span><span></span><span></span></div>
        <div class="incentive-card__footer"></div>
      </article>
      <article class="incentive-card theme-cruise">
        <div class="incentive-card__photo" role="img" aria-label="Cruise ship at sea">
          <p class="incentive-card__title">Enjoy <span class="incentive-card__tag">LUXURY CRUISE</span></p>
          <p class="incentive-card__note">4 Night Luxury Cruise Getaway</p>
        </div>
        <div class="incentive-card__band"></div>
        <div class="incentive-card__body"></div>
        <div class="incentive-card__thumbs" role="img" aria-label="Small cruise photos"><span></span><span></span><span></span></div>
        <div class="incentive-card__footer"></div>
      </article>

      <article class="incentive-card theme-dining">
        <div class="incentive-card__photo" role="img" aria-label="Restaurant dining scene">
          <p class="incentive-card__title">Enjoy <span class="incentive-card__tag">$400 OFF</span></p>
          <p class="incentive-card__note">$400 Off At Thousands Of Restaurants</p>
        </div>
        <div class="incentive-card__band"></div>
        <div class="incentive-card__body"></div>
        <div class="incentive-card__thumbs" role="img" aria-label="Small dining photos"><span></span><span></span><span></span></div>
        <div class="incentive-card__footer"></div>
      </article>
      <article class="incentive-card theme-tablet">
        <div class="incentive-card__photo" role="img" aria-label="HD tablet device">
          <p class="incentive-card__title">Enjoy <span class="incentive-card__tag">HD TABLET</span></p>
          <p class="incentive-card__note">Brand New HD Tablet</p>
        </div>
        <div class="incentive-card__band"></div>
        <div class="incentive-card__body"></div>
        <div class="incentive-card__thumbs" role="img" aria-label="Small tablet photos"><span></span><span></span><span></span></div>
        <div class="incentive-card__footer"></div>
      </article>
      <article class="incentive-card theme-player">
        <div class="incentive-card__photo" role="img" aria-label="MP4 media player">
          <p class="incentive-card__title">Enjoy <span class="incentive-card__tag">MP4 PLAYER</span></p>
          <p class="incentive-card__note">Touch Screen Media Player</p>
        </div>
        <div class="incentive-card__band"></div>
        <div class="incentive-card__body"></div>
        <div class="incentive-card__thumbs" role="img" aria-label="Small media player photos"><span></span><span></span><span></span></div>
        <div class="incentive-card__footer"></div>
      </article>
      <article class="incentive-card theme-speaker">
        <div class="incentive-card__photo" role="img" aria-label="Portable speaker on a beach">
          <p class="incentive-card__title">Enjoy <span class="incentive-card__tag">SPEAKER</span></p>
          <p class="incentive-card__note">Wireless Portable Speaker</p>
        </div>
        <div class="incentive-card__band"></div>
        <div class="incentive-card__body"></div>
        <div class="incentive-card__thumbs" role="img" aria-label="Small speaker photos"><span></span><span></span><span></span></div>
        <div class="incentive-card__footer"></div>
      </article>
      <article class="incentive-card theme-card">
        <div class="incentive-card__photo" role="img" aria-label="Health and pharmacy savings">
          <p class="incentive-card__title">Free <span class="incentive-card__tag">DISCOUNT CARD</span></p>
          <p class="incentive-card__note">Health Savings Discount Card</p>
        </div>
        <div class="incentive-card__band"></div>
        <div class="incentive-card__body"></div>
        <div class="incentive-card__thumbs" role="img" aria-label="Small health savings photos"><span></span><span></span><span></span></div>
        <div class="incentive-card__footer"></div>
      </article>

      <article class="incentive-card theme-hotel">
        <div class="incentive-card__photo" role="img" aria-label="Hotel suite interior">
          <p class="incentive-card__title">Enjoy <span class="incentive-card__tag">HOTEL STAY</span></p>
          <p class="incentive-card__note">3-Star Hotel Accommodations</p>
        </div>
        <div class="incentive-card__band"></div>
        <div class="incentive-card__body"></div>
        <div class="incentive-card__thumbs" role="img" aria-label="Small hotel photos"><span></span><span></span><span></span></div>
        <div class="incentive-card__footer"></div>
      </article>
      <article class="incentive-card theme-air">
        <div class="incentive-card__photo" role="img" aria-label="Airliner in the sky">
          <p class="incentive-card__title">Enjoy <span class="incentive-card__tag">AIR + HOTEL</span></p>
          <p class="incentive-card__note">Two Roundtrip Airfare With Hotel</p>
        </div>
        <div class="incentive-card__band"></div>
        <div class="incentive-card__body"></div>
        <div class="incentive-card__thumbs" role="img" aria-label="Small travel photos"><span></span><span></span><span></span></div>
        <div class="incentive-card__footer"></div>
      </article>
      <article class="incentive-card theme-dining">
        <div class="incentive-card__photo" role="img" aria-label="Restaurant dining scene">
          <p class="incentive-card__title">Enjoy <span class="incentive-card__tag">$25 OFF</span></p>
          <p class="incentive-card__note">$25 Off At Thousands Of Restaurants</p>
        </div>
        <div class="incentive-card__band"></div>
        <div class="incentive-card__body"></div>
        <div class="incentive-card__thumbs" role="img" aria-label="Small dining photos"><span></span><span></span><span></span></div>
        <div class="incentive-card__footer"></div>
      </article>
      <article class="incentive-card theme-shop">
        <div class="incentive-card__photo" role="img" aria-label="Shopping and services savings">
          <p class="incentive-card__title">Enjoy <span class="incentive-card__tag">$100 OFF</span></p>
          <p class="incentive-card__note">Get $100 Off At Local Merchants</p>
        </div>
        <div class="incentive-card__band"></div>
        <div class="incentive-card__body"></div>
        <div class="incentive-card__thumbs" role="img" aria-label="Small shopping photos"><span></span><span></span><span></span></div>
        <div class="incentive-card__footer"></div>
      </article>
      <article class="incentive-card theme-shop">
        <div class="incentive-card__photo" role="img" aria-label="Shopping and services savings">
          <p class="incentive-card__title">Enjoy <span class="incentive-card__tag">$400 OFF</span></p>
          <p class="incentive-card__note">Get $400 Off At Local Merchants</p>
        </div>
        <div class="incentive-card__band"></div>
        <div class="incentive-card__body"></div>
        <div class="incentive-card__thumbs" role="img" aria-label="Small shopping photos"><span></span><span></span><span></span></div>
        <div class="incentive-card__footer"></div>
      </article>
    </div>
  </section>
</body>
</html>
```